Business Card Design - Photographer

I am a landscape photographer and I require a business card design. 

I require two designs:
1)  a double sided business card
 and
b)  a single sided business card 

The single sided design can either be the same as the double sided (with just one side having all the information)....or it can be an entire new design. Its up to you.

My corporate colours are (CMYK):

Blue   69, 32, 0, 0
Grey  72,  64,  47,  31
Green  32,  2,  91,  0
Yellow   0, 19, 92, 0
Orange  0, 39, 75, 0

Colour space in final file should be in CMYK.

The details that need to be included on the card:

- Use the provided Logo
- Name: Wiktor Baranowski
- Email:   sales@vistalumeworks.com.au
- Website:    vistalumeworks.com.au
- Twitter:    twitter.com/vistalumeworks
- Facebook:   facebook.com/vistalumeworks
- Mobile  0417 539 662

Please use the attached template to design the logo to the specified size, including the marked bleed lines. I have also attached my logo in PNG (transparent background) and ai format for you to use.

The final file should be:
- Photoshop version with layers so I can edit the name/text etc. All non vector files should be high resolution at 1039 x 697 pixels at 300 dpi.

I also require a file as:
- Vector based PDF

Anyway questions please contact me.

Thank you

Industry/Entity Type

Landscape

Logo styles of interest
Pictorial/Combination Logo
Abstract Logo
Wordmark Logo
Lettermark Logo
Requirements
Must have
• The details that need to be included on the card:

- Use the provided Logo
- Name: Wiktor Baranowski
- Email: sales@vistalumeworks.com.au
- Website: vistalumeworks.com.au
- Twitter: twitter.com/vistalumeworks
- Facebook: facebook.com/vistalumeworks
- Mobile 0417 539 662

```html
<!DOCTYPE html>
<html lang="en">
<head>
<meta charset="utf-8">
<title>Vistalume Works – Business Card</title>
<link href="https://fonts.googleapis.com/css2?family=Cinzel:wght@500&family=Source+Sans+3:wght@400;600;700&display=swap" rel="stylesheet">
<style>
  :root {
    --stage: #2b3134;
    --card: #ffffff;
    --ink: #3b3f4f;
    --text: #2a2a2a;
    --orange: #f8a84a;
    --blue: #3e8fce;
    --green: #a9c93a;
    --yellow: #fbc90f;
  }
  * { margin: 0; padding: 0; box-sizing: border-box; }
  html, body { width: 987px; height: 1200px; overflow: hidden; }
  body {
    position: relative;
    background: var(--stage);
    font-family: "Source Sans 3", "Helvetica Neue", Arial, sans-serif;
    color: var(--text);
  }
  .card {
    position: absolute;
    background: var(--card);
    border-radius: 28px;
    overflow: hidden;
  }
  .card--front { left: 93px; top: 117px; width: 791px; height: 451px; }
  .card--back  { left: 91px; top: 637px; width: 790px; height: 450px; }

  .brand {
    position: absolute;
    left: 0; width: 100%;
    display: flex; flex-direction: column; align-items: center;
  }
  .brand__mark {
    border-radius: 50%;
    background: var(--ink);
  }
  .brand__name {
    font-family: "Cinzel", Georgia, serif;
    font-weight: 500;
    color: var(--ink);
    letter-spacing: 1px;
    white-space: nowrap;
  }
  .card--front .brand { top: 36px; }
  .card--front .brand__mark { width: 140px; height: 140px; margin-bottom: 28px; }
  .card--front .brand__name { font-size: 37px; line-height: 1; }

  .name-band {
    position: absolute; left: 0; top: 276px;
    width: 677px; height: 53px;
    background: var(--orange);
    display: flex; align-items: center; justify-content: center;
    padding-left: 40px;
  }
  .name-band__name { font-size: 29px; font-weight: 700; color: #111; }
  .name-band__role { font-size: 19px; font-weight: 400; color: #111; margin-left: 6px; }
  .name-band__role::before { content: "- "; font-size: 24px; }
  .accent-block {
    position: absolute; left: 688px; top: 276px;
    width: 103px; height: 53px;
    background: var(--blue);
  }

  .contacts {
    position: absolute; left: 0; top: 343px; width: 100%;
    list-style: none; text-align: center;
    font-size: 19px; line-height: 29px; color: var(--text);
  }
  .contacts b { font-weight: 700; }
  .contacts .sep { margin: 0 7px; }

  .card--back .brand { top: 44px; }
  .card--back .brand__mark { width: 250px; height: 250px; margin-bottom: 26px; }
  .card--back .brand__name { font-size: 30px; line-height: 1; }
  .website {
    position: absolute; left: 0; top: 396px; width: 100%;
    text-align: center; font-size: 26px; color: var(--ink);
    letter-spacing: 0.3px;
  }
</style>
</head>
<body>
  <section class="card card--front" aria-label="Business card front">
    <div class="brand">
      <span class="brand__mark" aria-hidden="true"></span>
      <span class="brand__name">VISTALUME WORKS</span>
    </div>
    <div class="name-band">
      <span class="name-band__name">Your Name</span>
      <span class="name-band__role">Adminsitrator</span>
    </div>
    <div class="accent-block"></div>
    <ul class="contacts">
      <li><b>m</b> : 0417 539 662</li>
      <li><b>e</b> : sales@vistalumeworks.com.au<span class="sep">|</span><b>w</b> : vistalumeworks.com.au</li>
      <li><b>t</b> : twitter.com/vistalumeworks<span class="sep">|</span><b>f</b> : facebook.com/vistalumeworks</li>
    </ul>
  </section>

  <section class="card card--back" aria-label="Business card back">
    <div class="brand">
      <span class="brand__mark" aria-hidden="true"></span>
      <span class="brand__name">VISTALUME WORKS</span>
    </div>
    <p class="website">www.vistalumeworks.com.au</p>
  </section>
</body>
</html>
```